Flyer for an pediatric sleep consultancy - to distribute to play and childcare centers etc.

I need a flyer that will attract the attention of parents with children between the age of babies to toddlers, who may be experiencing sleep issues. The flyer will be placed at places such as community centers, doctors room, play centers, kindergardens, etc.

My company is called "The Quiet Meadow Nest" and provides a sleep consultancy service. My service essentially provides a customized plan for parents to follow and general advice and guidance. It is not medical advice.

I like to the flyer to have an overall tone that is soft and peaceful with a clean and beautiful design, however can catch the attention of parents who may be struggling with their child's sleep issues and are sleep deprived. I would like photos with minimal text. The colour I use is a brownish rose. I will attach some of my designs to give you an idea. You can have a look at my homepage as well to get an idea about my esthetic direction and the colour. Although the colour of my page is a bit too brownish....

I will provide the text to appear in the flyer once I have a better idea of the layout that I prefer for the flyer. The text however wont be extensive, just some catchy points.

I want to direct people to my website which is www.quietmeadownest-example.com
I offer a first FREE evaluation call, to the parents, to get to know each other better, learn about their child's particular sleep problems and see if we are a good fit and can work together. I would like to have this information somehow on the flyer, so that the parents will contact me.
I also have a facebook page, which is: The Quiet Meadow Nest

I have a logo that I would like to appear on the flyer. I will attach the file once the uploader on pixel guild is fixed.

When I print the flyer - I like to print A5 SIZE ... please make sure the formatting is OK for this size.

Here are some text ideas. of course all of it would be too much, I guess. On the front of the flyer I would like to have some catchy phrase or something similar to get people interested and to want to know more. On the back there could be a bit more text and information. But I'm open too suggestions....
I'm not too sure about the wording yet. But here are some text that I might be use:

Is sleep an issue in your home?

Is your baby having trouble sleeping? ... are you?!
I can help!

Sleep, baby, sleep….

Teaching children how to sleep

The Quiet Meadow Nest is a pediatric sleep consultancy that specializes in helping parents with children who struggle to develop good and healthy sleep habits.
Disruptive sleep patterns or not enough sleep can affect the physical, mental and emotional development of your child.

Of course nobody plans to have a sleep problem, but habits can become easily ingrained and spiral quickly out of control and you can find yourself sleep deprived, desperate and not too sure what to do. You see all the other sleeping babies and wish there was someone who understood what you were going through?! Well, there is!

Contact me for a free 15 minute consultation.

This 15 minute „mini“ consultation is a chance to discuss your unique sleep challenges and sleep goals with me. I will provide you with an overview of how I will work with your family to achieve your wildest sleep dreams (goals).
Furthermore do I understand and believe that every child and their family is unique and there is no one size fits all!
I would love to have a chat with you and talk about how I can help make things easier for you and your family!

Do I need a sleep consultant for my child?
The answer is yes if:
- if your child will only fall asleep when nursing or bottle feeding
- if your child needs a dummy or other external aid, like being rocked, patted or taken for a care ride to fall asleep
- if your good night routine is a challenging and exhausting procedure instead of a relaxed and enjoyable moment for the whole family
- if sleep is a constant battle in your home which leaves you feeling frustrated and exhausted
- if your own lack of sleep is taking a toll on you and the whole family

What can I do for you?

I will:

- Guide you to set an age appropriate foundation for good sleep
- Create an individual sleep plan tailored especially to your child’s sleep needs and circumstances
- Help you to teach your childto go to sleep and get back to sleep independently during the night
- show you how to teach your child to take healthful, restorative naps
-Learn

Contact:

Marta Lindqvist
info@quietmeadownest-example.com
www.quietmeadownest-example.com
+34 612 384 705

Consultations in English, German or Spanish via Phone/Skype or home consultation
Updates

Project Deadline Extended
Reason: I have to go on a business trip and won't be able to choose a design until the deadline. During the trip I won't have time to give feedback and ask for changes. thank you

Target Market(s)

parents, sleep deprived mothers, young families, child care provider,

Industry/Entity Type

Baby Care

Contact Information for Business Card

Marta Lindqvist
pediatric sleep consultant
+34 612 384 705

```html
<!DOCTYPE html>
<html lang="en">
<head>
<meta charset="utf-8">
<title>The Quiet Meadow Nest – A5 Flyer</title>
<link href="https://fonts.googleapis.com/css2?family=Source+Sans+3:ital,wght@0,300;0,400;0,600;0,700;1,700&display=swap" rel="stylesheet">
<style>
  :root{
    --rose:#f2a59b;
    --rose-soft:#f5b8af;
    --rose-deep:#e8897d;
    --rose-text:#e27d70;
    --paper:#f3f3f3;
    --ink:#555;
    --ink-dark:#444;
    --stage:#ebe8e5;
    --white:#fff;
  }
  *{box-sizing:border-box;margin:0;padding:0}
  html,body{width:1200px;height:1176px;overflow:hidden}
  body{background:var(--stage);font-family:"Source Sans 3",sans-serif;color:var(--ink);position:relative}
  .flyer{position:absolute;top:191px;width:560px;height:793px;background:var(--paper);overflow:hidden;box-shadow:0 2px 10px rgba(0,0,0,.12)}
  .flyer--front{left:25px}
  .flyer--back{left:615px}
  .abs{position:absolute}
  .layer{position:absolute;left:0;top:0}
  .brand-name{position:absolute;left:340px;top:54px;width:210px;text-align:center;color:var(--white);font-weight:300;font-size:17px;letter-spacing:-.2px;white-space:nowrap}
  .brand-dot{position:absolute;left:430px;top:22px;width:28px;height:28px;border-radius:50%;border:2px solid var(--white)}
  .cloud-text{position:absolute;color:var(--white);text-align:center;line-height:1.15}
  .headline{position:absolute;left:0;width:560px;text-align:center;color:var(--rose-text);font-size:22.5px;font-weight:400}
  .subline{position:absolute;left:0;width:560px;text-align:center;color:var(--ink);font-size:19px;font-weight:300}
  .divider{position:absolute;left:50px;width:470px;border-top:1px dashed var(--rose)}
  .col{position:absolute;width:228px;font-size:11.7px;line-height:14.7px;text-align:justify;font-weight:400}
  .col p+p{margin-top:14.7px}
  .col-title{color:var(--rose-text);font-size:12px;margin-bottom:16px}
  .cta-box{position:absolute;left:300px;top:562px;width:228px;height:36px;background:var(--rose);color:var(--white);font-style:italic;font-weight:700;font-size:12px;line-height:15px;text-align:center;padding-top:3px}
  .offer-band{position:absolute;left:0;top:715px;width:560px;height:44px;background:var(--rose-deep);color:var(--white);text-align:center;font-size:11.5px;line-height:14.5px;padding-top:7px}
  .footer{position:absolute;top:766px;left:0;width:560px;font-size:11.5px;color:var(--ink-dark)}
  .footer span{position:absolute;display:flex;align-items:center;gap:5px;white-space:nowrap}
  .footer svg{width:11px;height:11px}
  .answer{position:absolute;left:32px;top:356px;font-size:18.5px;font-weight:400;color:var(--ink-dark)}
  .answer b{font-weight:700}
  .checklist{position:absolute;left:31px;top:396px;width:228px;height:302px;background:var(--rose);list-style:none;padding:12px 6px 0 6px;color:var(--white);font-size:12px;line-height:15px}
  .checklist li{display:flex;gap:4px;margin-bottom:15px}
  .checklist svg{flex:none;width:8px;height:8px;margin-top:4px}
  .services-title{position:absolute;left:293px;top:322px;color:var(--rose-text);font-size:15.5px}
  .services{position:absolute;left:293px;top:346px;width:248px;list-style:none;font-size:11.7px;line-height:14.7px;text-align:justify}
  .services li::before{content:"•";color:var(--rose);margin-right:6px}
  .contact{position:absolute;left:39px;top:712px;font-size:13px;line-height:17.5px;color:var(--ink-dark)}
  .contact .name{color:var(--rose-text)}
</style>
</head>
<body>

<!-- Front side -->
<section class="flyer flyer--front">
  <svg class="layer" width="560" height="400" viewBox="0 0 560 400" role="img" aria-label="Photo: toddler peeking over a white blanket in a cot">
    <defs>
      <linearGradient id="frontPhoto" x1="0" y1="0" x2="1" y2="1">
        <stop offset="0" stop-color="#cfd2d6"/>
        <stop offset=".5" stop-color="#e4e5e7"/>
        <stop offset="1" stop-color="#f7f7f7"/>
      </linearGradient>
    </defs>
    <rect width="560" height="380" fill="url(#frontPhoto)"/>
    <path d="M0,372 C180,378 380,372 560,352 L560,400 L0,400 Z" fill="#f3f3f3"/>
  </svg>
  <svg class="layer" width="560" height="130" viewBox="0 0 560 130">
    <path d="M274,0 C300,70 370,118 560,112 L560,0 Z" fill="var(--rose)"/>
  </svg>
  <div class="brand-dot"></div>
  <div class="brand-name">The Quiet Meadow Nest</div>

  <svg class="layer" width="560" height="420" viewBox="0 0 560 420">
    <g fill="var(--rose-soft)" stroke="#fff" stroke-width="2">
      <path d="M40,300 C18,300 14,270 34,262 C30,236 58,222 78,236 C86,206 130,200 140,230 C170,226 178,262 158,270 C176,286 160,304 140,300 Z"/>
    </g>
    <g fill="var(--rose)" stroke="#fff" stroke-width="3">
      <path d="M80,388 C44,390 34,350 62,338 C50,310 82,292 104,306 C112,268 150,248 180,256 C200,232 246,242 252,272 C260,250 300,260 298,290 C330,284 342,330 314,342 C330,372 300,392 276,384 C262,400 220,402 206,388 C170,402 120,402 80,388 Z"/>
    </g>
  </svg>
  <div class="cloud-text" style="left:22px;top:258px;width:130px;font-size:15px;font-weight:300">Sleep, baby,<br>sleep....</div>
  <div class="cloud-text" style="left:60px;top:310px;width:240px;font-size:24px;font-weight:300;line-height:27px">Is sleep an issue<br>in your home?</div>

  <h1 class="headline" style="top:408px;left:0;padding-left:10px">Is your baby having trouble sleeping? ... are you?!</h1>
  <p class="subline" style="top:440px;padding-left:10px">I CAN HELP!</p>
  <div class="divider" style="top:470px"></div>

  <div class="col" style="left:36px;top:490px">
    <p class="col-title">Teaching children how to sleep</p>
    <p>The Quiet Meadow Nest is a pediatric sleep consultancy that specializes in helping parents with children who struggle to develop good and healthy sleep habits. Disruptive sleep patterns or not enough sleep can affect the physical, mental and emotional development of your child.</p>
    <p>Of course nobody plans to have a sleep problem, but habits can become easily ingrained and spiral quickly out of control and you can find yourself sleep deprived,</p>
  </div>
  <div class="col" style="left:300px;top:490px">
    <p>desperate and not too sure what to do. You see all the other sleeping babies and wish there was someone who understood what you were going through?! <b><i>Well, there is!</i></b></p>
  </div>
  <div class="cta-box">Contact me for a free 15 minute<br>consultation at +34 612 384 705</div>
  <div class="col" style="left:300px;top:608px">
    <p>This 15 minute „mini“ consultation is a chance to discuss your unique sleep challenges and sleep goals with me. I will provide you with an overview of how I will work with your family to achieve your wildest sleep dreams (goals).</p>
  </div>

  <div class="offer-band">First FREE evaluation call, to the parents, to get to know each other better, learn about<br>their child's particular sleep problems and see if we are a good fit and can work together!</div>

  <div class="footer">
    <span style="left:22px">
      <svg viewBox="0 0 12 12"><circle cx="6" cy="6" r="6" fill="var(--rose-deep)"/><rect x="3" y="4" width="6" height="4" fill="none" stroke="#fff" stroke-width=".9"/><path d="M3,4 L6,6.3 L9,4" fill="none" stroke="#fff" stroke-width=".9"/></svg>
      info@quietmeadownest-example.com
    </span>
    <span style="left:240px">
      <svg viewBox="0 0 12 12"><circle cx="6" cy="6" r="5.3" fill="none" stroke="var(--rose-deep)" stroke-width="1.2"/><path d="M4.2,3.4 C3.6,4 3.8,5.8 5.4,7.2 C6.8,8.4 8,8.6 8.6,8 L7.6,7 L6.9,7.4 C6.3,7 5.2,6 4.8,5.2 L5.2,4.5 Z" fill="var(--rose-deep)"/></svg>
      +34 612 384 705
    </span>
    <span style="left:388px">
      <svg viewBox="0 0 12 12"><circle cx="6" cy="6" r="5.3" fill="none" stroke="var(--rose-deep)" stroke-width="1.2"/><circle cx="6" cy="6" r="3" fill="none" stroke="var(--rose-deep)" stroke-width="1"/></svg>
      quietmeadownest-example.com
    </span>
  </div>
</section>

<!-- Back side -->
<section class="flyer flyer--back">
  <svg class="layer" width="560" height="320" viewBox="0 0 560 320" role="img" aria-label="Photo: newborn sleeping in a white round crib">
    <defs>
      <linearGradient id="backPhoto" x1="0" y1="0" x2="1" y2="1">
        <stop offset="0" stop-color="#e2e3e5"/>
        <stop offset=".6" stop-color="#f1f1f2"/>
        <stop offset="1" stop-color="#e6e4e3"/>
      </linearGradient>
    </defs>
    <rect width="560" height="310" fill="url(#backPhoto)"/>
    <path d="M0,178 C140,262 340,306 560,290 L560,320 L0,320 Z" fill="#f3f3f3"/>
  </svg>
  <svg class="layer" width="560" height="130" viewBox="0 0 560 130">
    <path d="M274,0 C300,70 370,118 560,112 L560,0 Z" fill="var(--rose)"/>
  </svg>
  <div class="brand-dot"></div>
  <div class="brand-name">The Quiet Meadow Nest</div>

  <svg class="layer" width="560" height="340" viewBox="0 0 560 340">
    <path d="M44,320 C18,320 14,286 38,278 C36,256 60,248 76,258 C78,226 110,208 140,212 C166,206 190,230 186,256 C206,252 232,262 230,282 C252,290 244,322 220,320 Z" fill="var(--rose)" stroke="#fff" stroke-width="3"/>
  </svg>
  <div class="cloud-text" style="left:24px;top:262px;width:216px;font-size:17px;font-weight:400;line-height:22px">Do I need a sleep<br>consultant for my child?</div>

  <p class="answer">The answer is <b>YES</b> if:</p>
  <ul class="checklist">
    <li><svg viewBox="0 0 10 10"><path d="M1,5 L4,8 L9,1" fill="none" stroke="#fff" stroke-width="1.8"/></svg><span>if your child will only fall asleep<br>when nursing or bottle feeding</span></li>
    <li><svg viewBox="0 0 10 10"><path d="M1,5 L4,8 L9,1" fill="none" stroke="#fff" stroke-width="1.8"/></svg><span>if your child needs a dummy or other external aid, like being rocked, patted or taken for a care ride to fall asleep</span></li>
    <li><svg viewBox="0 0 10 10"><path d="M1,5 L4,8 L9,1" fill="none" stroke="#fff" stroke-width="1.8"/></svg><span>if your good night routine is a challenging and exhausting procedure instead of a relaxed and enjoyable moment for the whole family</span></li>
    <li><svg viewBox="0 0 10 10"><path d="M1,5 L4,8 L9,1" fill="none" stroke="#fff" stroke-width="1.8"/></svg><span>if sleep is a constant battle in your home which leaves you feeling frustrated and exhausted</span></li>
    <li><svg viewBox="0 0 10 10"><path d="M1,5 L4,8 L9,1" fill="none" stroke="#fff" stroke-width="1.8"/></svg><span>if your own lack of sleep is taking<br>a toll on you and the whole family</span></li>
  </ul>

  <h2 class="services-title" style="font-weight:400">What can I do for you?</h2>
  <ul class="services">
    <li>Guide you to set an age appropriate foundation for good sleep</li>
    <li>Create an individual sleep plan tailored especially to your child’s sleep needs and circumstances</li>
    <li>Help you to teach your childto go to sleep and get back to sleep independently during the night</li>
    <li>Show you how to teach your child to take healthful, restorative naps</li>
    <li>Learn</li>
  </ul>

  <div class="abs" role="img" aria-label="Photo: the sleep consultant holding a toddler" style="left:266px;top:500px;width:294px;height:293px;background:linear-gradient(160deg,#eeeeee 0%,#e3e0dd 55%,#d6d2ce 100%)"></div>

  <div class="contact">
    <div class="name">Marta Lindqvist</div>
    <div>info@quietmeadownest-example.com</div>
    <div>www.quietmeadownest-example.com</div>
    <div>+34 612 384 705</div>
  </div>
</section>

</body>
</html>
```